Modern business card design for professional copywriter

I'd like a business card design that I can use to have my cards printed out by quillprint.com as a squared corners business card (see artwork and design guidelines here: https://help.quillprint.com/hc/en-gb/sections/200570950-QUILL-Product-Templates)

The design should be clean and modern and reflect the colours, tone and branding on my website: https://tessavorrin.com.au

Target Market(s)

Professionals, B2B small business owners

Industry/Entity Type

Business

Contact Information for Business Card

Tessa Vorrin
m: 0468 905 327
e: tessa@tessavorrin.com.au
w: tessavorrin.com.au

Font styles to use
Sans Serif

Requirements
Must have
• Tagline: "Smart copywriting for clever business people"
• Brand colours: fd8000, 009984, 666666 and black
Nice to have

```html
<!DOCTYPE html>
<html lang="en">
<head>
<meta charset="utf-8">
<title>Tessa Vorrin – Business Card</title>
<link rel="stylesheet" href="https://fonts.googleapis.com/css2?family=Open+Sans:wght@400;600;700&display=swap">
<style>
  :root {
    --page-bg: #f1f1f1;
    --card-green: #6f8b6c;
    --brand-orange: #fd8000;
    --brand-teal: #009984;
    --brand-grey: #666666;
    --text-light: #f4f4ee;
  }
  * { box-sizing: border-box; margin: 0; padding: 0; }
  html, body {
    width: 1200px; height: 533px; overflow: hidden;
    background: var(--page-bg);
    font-family: "Open Sans", sans-serif;
  }
  .stage { position: relative; width: 1200px; height: 533px; }
  .card {
    position: absolute; top: 85px; width: 541px; height: 311px;
    background: var(--card-green);
    border-left: 14px solid var(--brand-orange);
    box-shadow: 0 6px 18px rgba(0,0,0,0.18);
  }
  .card--front { left: 60px; }
  .card--back { left: 620px; }

  .wordmark {
    display: flex; align-items: center; gap: 8px;
    color: var(--brand-teal); font-weight: 600; font-size: 25px; letter-spacing: -0.3px;
  }
  .wordmark__dot {
    width: 16px; height: 16px; border-radius: 50%; background: var(--brand-orange);
  }
  .card--front .wordmark { position: absolute; left: 14px; top: 128px; }

  .divider {
    position: absolute; left: 259px; top: 100px; width: 1px; height: 158px;
    background: var(--brand-orange);
  }
  .identity { position: absolute; left: 290px; top: 66px; }
  .identity__name { font-size: 13px; font-weight: 700; color: #fff; letter-spacing: 0.3px; }
  .identity__name span { color: var(--brand-orange); }
  .identity__role { font-size: 8px; color: var(--text-light); letter-spacing: 0.4px; margin-top: 2px; }

  .contacts { position: absolute; left: 249px; top: 125px; list-style: none; }
  .contact { display: flex; align-items: center; height: 20px; margin-bottom: 19px; }
  .contact__badge {
    width: 20px; height: 20px; border-radius: 50%; background: var(--text-light);
    color: var(--brand-orange); font-size: 8px; font-weight: 700;
    display: flex; align-items: center; justify-content: center;
  }
  .contact__value {
    margin-left: 22px; font-size: 8px; color: var(--brand-orange); letter-spacing: 0.3px;
    text-transform: uppercase;
  }

  .card--back .brand-block {
    position: absolute; left: 0; right: 0; top: 124px;
    display: flex; flex-direction: column; align-items: center;
  }
  .tagline {
    margin-top: 14px; font-size: 8.5px; font-weight: 600; color: var(--text-light);
    letter-spacing: 0.4px; text-transform: uppercase;
  }
</style>
</head>
<body>
<main class="stage">
  <section class="card card--front" aria-label="Card front">
    <div class="wordmark"><span class="wordmark__dot"></span>Tessa Vorrin</div>
    <div class="divider"></div>
    <div class="identity">
      <p class="identity__name">TESSA <span>VORRIN</span></p>
      <p class="identity__role">COPYWRITER</p>
    </div>
    <ul class="contacts">
      <li class="contact"><span class="contact__badge">M</span><span class="contact__value">0468 905 327</span></li>
      <li class="contact"><span class="contact__badge">E</span><span class="contact__value">tessa@tessavorrin.com.au</span></li>
      <li class="contact"><span class="contact__badge">W</span><span class="contact__value">tessavorrin.com.au</span></li>
    </ul>
  </section>

  <section class="card card--back" aria-label="Card back">
    <div class="brand-block">
      <div class="wordmark"><span class="wordmark__dot"></span>Tessa Vorrin</div>
      <p class="tagline">Smart copywriting for clever business people</p>
    </div>
  </section>
</main>
</body>
</html>
```